A5 Patient Information Booklet (Chiropractic Clinic) 4-8 pages

Here’s a polished, professional rewrite of your full brief and content, with clearer structure, corrected language, and a premium tone:

---

**Project Title:** Premium Patient Information Brochure (Chiropractic & Wellness Clinic)

---

### **Overview**

We are a health and wellness clinic seeking a premium, high-end patient information brochure to provide following a patient’s initial consultation and first treatment.

The purpose of this booklet is to:

* Reinforce trust and professionalism
* Help patients understand what to expect next
* Encourage adherence to care recommendations
* Position the clinic as calm, expert-led, and results-driven

---

### **Format**

* 4–8 page booklet (A5 or similar size)
* Print-ready and digital versions required

---

### **Target Audience**

Patients who have just completed their initial consultation and may have begun treatment. They may already be experiencing physical or mental changes, so the brochure should guide, reassure, and educate them on what comes next.

---

### **Tone & Style**

* Premium, calm, and reassuring
* Modern wellness aesthetic (not overly clinical)
* Clean layout with minimal clutter
* Soft, neutral colour palette (whites, creams, muted greens, soft blues)
* Elegant typography (e.g. Montserrat / Lato)
* High-end, trustworthy, and professional feel

---

### **Key Messages**

#### 1. Listen to Your Body

Patients may feel different after treatment. Reassure them that this is normal and part of the healing process.

#### 2. Post-Treatment Advice

* Stay well hydrated
* Rest if needed
* Avoid overexertion if the body requires recovery

#### 3. Healing is a Journey (Core Concept)

A strong visual metaphor of a **“road to recovery”** or **journey** should be central to the design.

This journey should clearly illustrate three phases:

* **Phase 1: Initial Care (Weeks 1–6)**
Focus: Reducing pain/discomfort, calming the body, and initiating response to treatment

* **Phase 2: Corrective Care (Weeks 6–12)**
Focus: Addressing underlying issues, improving function, and creating lasting change

* **Phase 3: Wellness / Maintenance (Ongoing)**
Focus: Maintaining progress, preventing relapse, and supporting long-term wellbeing

**Important:**

* Emphasise that this is not a quick fix
* Progress requires time and consistency
* Each patient follows an individualised care plan
* The journey should feel structured, positive, and achievable

#### 4. Personalised Care

Reinforce that every treatment plan is tailored specifically to the individual.

#### 5. Professional Reassurance

Patients should feel confident they are in expert hands and supported throughout their journey.

---

### **Design Direction**

* Use imagery that reflects calmness, progression, and wellness (e.g. pathways, nature, soft gradients)
* Avoid generic stock imagery
* **Only use original clinic images from website and social media**
* Prioritise white space and clarity
* Aim for a luxury spa/medical hybrid aesthetic

---

## **Content Structure (Page-by-Page)**

### **Front Cover**

* Clean, minimal, premium design
* Clinic branding

---

### **Page 1: Patient Case Summary**

**Title:** *Welcome to Fernwell Spine Studio*

Thank you for choosing Fernwell Spine Studio.

This booklet is designed to guide you through:

* What we found during your initial consultation
* Your personalised recommended treatment plan
* Your road to recovery
* Long-term wellness care
* Why we take the approach we do

---

### **Page 2: Your Care Journey**

**Stage 1: Your Initial Consultation**

Today we completed a comprehensive assessment of your health and function, including:

* Full case history and discussion of your symptoms and goals
* Orthopaedic and neurological testing
* Postural and movement assessment
* Initial treatment (where appropriate)

**What this tells us:**

* How your body is currently functioning
* Where areas of stress or dysfunction may be present
* The most appropriate and effective path forward for your care

---

### **Page 3: Your Suggested Treatment Plan**

Based on today’s findings, your recommended care plan is:

**______ treatments over ______ weeks**

This should be viewed alongside your *Road to Recovery* to help you understand what to expect.

We have also discussed:

* Expected timelines for improvement
* Available payment options

**After Treatment:**
It is common to feel different following treatment. This is a normal response as your body begins to adapt and respond.

We recommend:

* Staying well hydrated
* Allowing time for rest and recovery
* Avoiding overexertion if your body feels it needs it

---

### **Page 4: What to Expect Next**

Healing is not always linear—it is a process that occurs over time.

Your care will typically progress through the following stages:

* **Relief Care**
Focused on reducing discomfort and calming the body

* **Corrective Care**
Focused on addressing underlying issues and improving function
(This phase may include prescribed exercises)

* **Maintenance / Wellness Care**
Focused on sustaining progress, preventing recurrence, and supporting long-term health

---

### **Page 5: Understanding Chiropractic Care**

**What is Chiropractic?**
Chiropractic care focuses on the relationship between the spine, nervous system, and overall body function.

By improving spinal movement and alignment, chiropractic care helps support the nervous system, allowing the body to function and heal more effectively.

**About Fernwell Spine Studio**
At Fernwell Spine Studio, our approach is centred around personalised, patient-focused care. We aim to not only relieve symptoms but to address underlying causes and support long-term wellbeing.

---

### **Back Page**

* Clinic contact details
* Website
* Social media icons/handles

**Closing Message:**
“A healthier, stronger you—supported every step of the way.”

---

### **Deliverables**

* Print-ready PDF
* Editable source files

---

### **Additional Notes**

* The brochure should feel valuable and worth keeping
* Encourage long-term care in a subtle, non-pushy way
* Maintain clarity, readability, and strong visual hierarchy
* Balance professionalism with warmth and approachability

---

If you’d like, I can also turn this into **actual brochure copy (fully written, patient-facing text)** or help you refine it further for a designer.

Existing patients who want to feel better and look after themselves that is given after their initil consultation appointment

Chiropractic, wellness, health

• Montserrat or Lato

0094D4
00A9DD
6FCCEA
C7EBF8
E9F6FB
00AB8E
00BBA5
67D7C9
C6EFE9
E9F9F6
6B429C
8869AF
B7A5CE
E3DAEB
F3F0F8

• my own photos, look premium wellness, be clear and simple to understand for patients journey or what to expect next and over time
• USe my social media/website for ideas
• generic photos and images

```html
<!DOCTYPE html>
<html lang="en">
<head>
<meta charset="utf-8">
<title>Fernwell Spine Studio – Patient Information Brochure</title>
<link rel="stylesheet" href="https://fonts.googleapis.com/css2?family=Outfit:wght@400;500;600;700&family=Anton&display=swap">
<style>
:root{
  --stage:#111111;
  --ink:#3a2a24;
  --teal:#13aaa5;
  --teal-deep:#00ab8e;
  --pink:#f77fbf;
  --pink-soft:#fdf0f6;
  --purple:#b58fd4;
  --blue:#5fb4e4;
  --white:#ffffff;
  --head:"Outfit", sans-serif;
  --display:"Anton", sans-serif;
}
*{margin:0;padding:0;box-sizing:border-box}
html,body{width:1085px;height:1200px;overflow:hidden;background:var(--stage)}
body{position:relative;font-family:var(--head);color:var(--ink)}
.spread{position:absolute;left:181px;width:723px;height:482px;overflow:hidden}
.spread--outside{top:107px}
.spread--inside{top:611px}
.spread-bg{position:absolute;inset:0}
.panel{position:absolute;top:0;width:241px;height:482px}
.panel--1{left:0}.panel--2{left:241px}.panel--3{left:482px}
.abs{position:absolute}
h2.section-title{font-weight:600;font-size:19px;line-height:23px;color:var(--ink)}
.rule{position:absolute;width:33px;height:2px;background:var(--teal)}
.body-copy{font-size:8.6px;line-height:12.5px;font-weight:500;text-align:justify}
.bullets{list-style:none}
.bullets li{position:relative;padding-left:12px}
.bullets li::before{content:"";position:absolute;left:0;top:.38em;width:7px;height:7px;border-radius:50%;background:var(--dot,var(--purple))}
/* outside spread */
.contact-label{font-family:var(--display);font-size:10px;letter-spacing:.3px;color:var(--ink)}
.contact-text{font-size:9px;line-height:14px;font-weight:500}
.contact-icon{position:absolute;left:-19px;top:0}
.social{position:absolute;width:25px;height:25px;border-radius:50%;background:linear-gradient(135deg,#d88ad0,#7aa8e6)}
.closing{font-size:16px;line-height:18.5px;font-weight:600}
.cover-title{font-family:var(--display);color:var(--white);font-size:20px;line-height:24px;text-align:center;letter-spacing:.5px;-webkit-text-stroke:1px var(--ink);paint-order:stroke fill}
.cover-sub{font-size:16px;line-height:19px;text-align:center;color:var(--white);font-weight:400;text-shadow:0 0 1px var(--ink),0 0 1px var(--ink)}
.guide-title{font-size:13px;line-height:15px;text-align:center;color:var(--white);font-weight:600}
.guide-list{list-style:none;color:var(--white);font-size:8.5px;line-height:12.5px;font-weight:500}
.guide-list li{position:relative;padding-left:11px}
.guide-list li::before{content:"";position:absolute;left:0;top:3px;width:6px;height:6px;border-radius:50%;border:1px solid var(--white)}
.brand-name{font-size:10px;line-height:12px;font-weight:600;color:var(--ink);text-align:center}
/* inside spread */
.lead{font-size:11px;line-height:13px;font-weight:600}
.list-10{font-size:10px;line-height:12.5px}
.list-10 li{margin-bottom:3px}
.plan-title{font-size:17px;line-height:20px;font-weight:600;color:var(--white)}
.plan-blank{font-size:11px;font-weight:500;color:var(--white)}
.caption{font-size:7.5px;line-height:9px;color:var(--white);text-align:center}
.plan-head{font-size:12px;font-weight:600;color:var(--white)}
.plan-list{color:var(--white);font-size:10px;line-height:15px;--dot:var(--pink)}
.plan-text{color:var(--white);font-size:9px;line-height:11px}
.teal-lead{font-size:11px;line-height:13px;font-weight:600;color:var(--teal);text-align:justify}
.stage-title{font-size:10.5px;font-weight:500}
.stage-text{font-size:9px;line-height:11px}
</style>
</head>
<body>

<section class="spread spread--outside">
  <svg class="spread-bg" width="723" height="482" viewBox="0 0 723 482">
    <defs>
      <linearGradient id="coverGrad" x1="0" y1="0" x2="0" y2="1">
        <stop offset="0" stop-color="#de8bc8"/>
        <stop offset=".35" stop-color="#b39bd9"/>
        <stop offset=".62" stop-color="#6fb7e6"/>
      </linearGradient>
      <linearGradient id="lowerGrad" x1="0" y1="0" x2="0" y2="1">
        <stop offset="0" stop-color="#c59ad8"/>
        <stop offset="1" stop-color="#62b3e5"/>
      </linearGradient>
      <linearGradient id="photoWarm" x1="0" y1="0" x2="1" y2="1">
        <stop offset="0" stop-color="#d9cfc6"/>
        <stop offset="1" stop-color="#8d7468"/>
      </linearGradient>
      <linearGradient id="photoMono" x1="0" y1="0" x2="1" y2="1">
        <stop offset="0" stop-color="#c9c9c9"/>
        <stop offset="1" stop-color="#4a4a4a"/>
      </linearGradient>
      <clipPath id="coverClip"><rect x="482" y="0" width="241" height="482"/></clipPath>
    </defs>
    <rect x="0" y="0" width="241" height="482" fill="#ffffff"/>
    <rect x="241" y="0" width="241" height="482" fill="#fdf0f6"/>
    <rect x="482" y="0" width="241" height="482" fill="url(#coverGrad)"/>
    <path d="M0,327 C70,348 130,360 175,345 C208,333 230,312 241,290 L241,482 L0,482Z" fill="#f77fbf"/>
    <path d="M0,332 C70,358 135,372 185,362 C215,355 234,338 241,326 L241,482 L0,482Z" fill="#13aaa5"/>
    <g role="img" aria-label="Photo of a chiropractor treating a patient's shoulder">
      <circle cx="133" cy="390" r="67" fill="#ffffff"/>
      <circle cx="133" cy="390" r="64" fill="url(#photoMono)"/>
    </g>
    <path d="M241,292 C256,330 292,356 342,360 C402,364 452,350 482,330 L482,482 L241,482Z" fill="#f77fbf"/>
    <path d="M241,318 C263,350 302,368 352,370 C407,372 452,360 482,345 L482,482 L241,482Z" fill="url(#lowerGrad)" stroke="#ffffff" stroke-width="2"/>
    <circle cx="362" cy="427" r="42" fill="none" stroke="#ffffff" stroke-opacity=".45" stroke-width="1.5"/>
    <g clip-path="url(#coverClip)">
      <path d="M482,325 C560,332 660,322 723,305 L723,482 L482,482Z" fill="#13aaa5"/>
      <circle cx="603" cy="228" r="130" fill="#f77fbf"/>
      <circle cx="600" cy="222" r="120" fill="#13aaa5"/>
      <g role="img" aria-label="Photo of the chiropractor assessing a smiling patient's back">
        <circle cx="603" cy="223" r="110" fill="#ffffff"/>
        <circle cx="603" cy="223" r="107" fill="url(#photoWarm)"/>
      </g>
      <circle cx="670" cy="224" r="52" fill="#ffffff"/>
    </g>
  </svg>

  <div class="panel panel--1">
    <h2 class="section-title abs" style="left:23px;top:30px">What is Chiropractic</h2>
    <span class="rule" style="left:23px;top:57px"></span>
    <div class="abs" style="left:23px;top:70px;width:196px">
      <p class="body-copy">Chiropractic care focuses on the relationship between the spine, nervous system, and overall body function.</p>
      <p class="body-copy" style="margin-top:12px">By improving spinal movement and alignment, chiropractic care helps support the nervous system, allowing the body to function and heal more effectively.</p>
    </div>
    <h2 class="section-title abs" style="left:23px;top:183px;width:210px">About<br>Fernwell Spine Studio</h2>
    <span class="rule" style="left:23px;top:234px"></span>
    <p class="body-copy abs" style="left:23px;top:244px;width:196px">At Fernwell Spine Studio, our approach is centred around personalised, patient-focused care. We aim to not only relieve symptoms but to address underlying causes and support long-term wellbeing.</p>
  </div>

  <div class="panel panel--2">
    <h2 class="section-title abs" style="left:20px;top:30px">Contact Us</h2>
    <span class="rule" style="left:20px;top:57px"></span>
    <div class="abs" style="left:40px;top:72px">
      <svg class="contact-icon" width="13" height="13" viewBox="0 0 13 13"><circle cx="6.5" cy="6.5" r="5.5" fill="none" stroke="#8f9fe0" stroke-width="1.2"/><ellipse cx="6.5" cy="6.5" rx="2.4" ry="5.5" fill="none" stroke="#8f9fe0" stroke-width="1"/><path d="M1,6.5H12M2,3.8H11M2,9.2H11" stroke="#8f9fe0" stroke-width=".9"/></svg>
      <div class="contact-label">WEBSITE</div>
      <div class="contact-text">https://www.fernwellspinestudio.com/</div>
    </div>
    <div class="abs" style="left:40px;top:106px">
      <svg class="contact-icon" width="12" height="15" viewBox="0 0 12 15"><path d="M6,14.5C2.5,10 1,7.5 1,5.5a5,5 0 0 1 10,0C11,7.5 9.5,10 6,14.5Z" fill="#c58bd4"/><circle cx="6" cy="5.5" r="2" fill="#ffffff"/></svg>
      <div class="contact-label">ADDRESS</div>
      <div class="contact-text">Fernwell Spine Studio<br>Chiropractic &amp; Wellness<br>12 Mill Lane, Ashbury<br>AB1 4FS</div>
    </div>
    <span class="social" style="left:40px;top:203px" aria-label="Social profile"></span>
    <span class="social" style="left:67px;top:203px" aria-label="Social profile"></span>
    <p class="closing abs" style="left:42px;top:240px;width:170px">A healthier, stronger you—supported every step of the way.</p>
  </div>

  <div class="panel panel--3">
    <h1 class="cover-title abs" style="left:0;top:14px;width:241px">WELCOME TO<br>FERNWELL SPINE STUDIO</h1>
    <p class="cover-sub abs" style="left:0;top:64px;width:241px">Thank you for choosing<br>Fernwell Spine Studio.</p>
    <p class="brand-name abs" style="left:148px;top:212px;width:80px">Fernwell<br>Spine Studio</p>
    <h3 class="guide-title abs" style="left:0;top:367px;width:241px">This booklet is designed<br>to guide you through:</h3>
    <ul class="guide-list abs" style="left:19px;top:405px;width:220px">
      <li>What we found during your initial consultation</li>
      <li>Your personalised recommended treatment plan</li>
      <li>Your road to recovery</li>
      <li>Long-term wellness care</li>
      <li>Why we take the approach we do</li>
    </ul>
  </div>
</section>

<section class="spread spread--inside">
  <svg class="spread-bg" width="723" height="482" viewBox="0 0 723 482">
    <defs>
      <linearGradient id="planGrad" x1="0" y1="0" x2="0" y2="1">
        <stop offset="0" stop-color="#d98cc9"/>
        <stop offset=".4" stop-color="#9f9fdc"/>
        <stop offset="1" stop-color="#3d9dd4"/>
      </linearGradient>
      <linearGradient id="swoosh" x1="0" y1="0" x2="1" y2="0">
        <stop offset="0" stop-color="#d59ad6"/>
        <stop offset="1" stop-color="#a59ad9"/>
      </linearGradient>
      <linearGradient id="photoBed" x1="0" y1="0" x2="1" y2="1">
        <stop offset="0" stop-color="#d8cbbd"/>
        <stop offset="1" stop-color="#9c8271"/>
      </linearGradient>
      <linearGradient id="photoRoom" x1="0" y1="0" x2="1" y2="1">
        <stop offset="0" stop-color="#e2ddd2"/>
        <stop offset="1" stop-color="#9a8470"/>
      </linearGradient>
      <linearGradient id="photoMono2" x1="0" y1="0" x2="1" y2="1">
        <stop offset="0" stop-color="#cfcfcf"/>
        <stop offset="1" stop-color="#404040"/>
      </linearGradient>
      <linearGradient id="chartGrad" x1="0" y1="1" x2="1" y2="0">
        <stop offset="0" stop-color="#f3f3f3"/>
        <stop offset=".5" stop-color="#f9f5e8"/>
        <stop offset="1" stop-color="#eaf6f1"/>
      </linearGradient>
    </defs>
    <rect x="0" y="0" width="241" height="200" fill="url(#photoBed)" role="img" aria-label="Photo of a patient lying face down receiving back treatment"/>
    <path d="M0,114 C80,95 182,100 241,188 L241,482 L0,482Z" fill="url(#swoosh)"/>
    <path d="M0,120 C80,106 178,116 241,200 L241,482 L0,482Z" fill="#ffffff"/>
    <rect x="241" y="0" width="241" height="482" fill="url(#planGrad)"/>
    <g role="img" aria-label="Road to Recovery chart showing progress from suffering to optimising over days, weeks, months and years">
      <rect x="271" y="113" width="180" height="128" fill="#3b3b3b"/>
      <rect x="275" y="117" width="172" height="120" fill="url(#chartGrad)"/>
      <rect x="275" y="117" width="5" height="120" fill="#e0c34a"/>
      <rect x="275" y="232" width="172" height="5" fill="#d8262f"/>
    </g>
    <rect x="482" y="0" width="241" height="190" fill="url(#photoRoom)" role="img" aria-label="Photo of the clinic treatment room with an adjusting table"/>
    <path d="M482,160 C530,120 620,104 723,106 L723,482 L482,482Z" fill="url(#swoosh)"/>
    <path d="M482,170 C535,132 620,116 723,116 L723,482 L482,482Z" fill="#ffffff"/>
    <circle cx="645" cy="145" r="70" fill="#7cb6ea"/>
    <circle cx="648" cy="144" r="68" fill="#b39ad8"/>
    <g role="img" aria-label="Photo of the chiropractor treating a male patient's shoulder">
      <circle cx="649" cy="145" r="66" fill="#ffffff"/>
      <circle cx="649" cy="145" r="64" fill="url(#photoMono2)"/>
    </g>
  </svg>

  <div class="panel panel--1">
    <h2 class="section-title abs" style="left:23px;top:145px">Your Initial<br>Consultation</h2>
    <span class="rule" style="left:23px;top:197px"></span>
    <p class="lead abs" style="left:23px;top:208px;width:208px">Today we completed a comprehensive assessment of your health and function, including:</p>
    <ul class="bullets list-10 abs" style="left:23px;top:256px;width:210px">
      <li>Full case history and discussion of your symptoms and goals</li>
      <li>Orthopaedic and neurological testing</li>
      <li>Postural and movement assessment</li>
      <li>Initial treatment (where appropriate)</li>
    </ul>
    <h2 class="section-title abs" style="left:23px;top:345px">What this Tells Us</h2>
    <span class="rule" style="left:23px;top:372px"></span>
    <ul class="bullets list-10 abs" style="left:23px;top:381px;width:210px">
      <li>How your body is currently functioning</li>
      <li>Where areas of stress or dysfunction may be present</li>
      <li>The most appropriate and effective path forward for your care</li>
    </ul>
  </div>

  <div class="panel panel--2">
    <h2 class="plan-title abs" style="left:16px;top:22px;width:215px">Based on today’s findings, your recommended care plan is:</h2>
    <p class="plan-blank abs" style="left:16px;top:90px">_____ treatments over _____ weeks</p>
    <p class="caption abs" style="left:10px;top:250px;width:221px">This should be viewed alongside your<br>*Road to Recovery* to help you understand what to expect.</p>
    <h3 class="plan-head abs" style="left:16px;top:283px">WE HAVE ALSO DISCUSSED:</h3>
    <ul class="bullets plan-list abs" style="left:16px;top:299px">
      <li>Expected timelines for improvement</li>
      <li>Available payment options</li>
    </ul>
    <h3 class="plan-head abs" style="left:16px;top:339px">AFTER TREATMENT:</h3>
    <p class="plan-text abs" style="left:16px;top:354px;width:218px">It is common to feel different following treatment. This is a normal response as your body begins to adapt and respond.</p>
    <h3 class="plan-head abs" style="left:16px;top:402px">WE RECOMMEND:</h3>
    <ul class="bullets plan-list abs" style="left:16px;top:416px;width:210px">
      <li>Staying well hydrated</li>
      <li>Allowing time for rest and recovery</li>
      <li>Avoiding overexertion if your body feels it needs it</li>
    </ul>
  </div>

  <div class="panel panel--3">
    <h2 class="section-title abs" style="left:20px;top:186px">What to<br>Expect Next</h2>
    <span class="rule" style="left:20px;top:238px"></span>
    <p class="lead abs" style="left:20px;top:248px;width:205px;text-align:justify">Healing is not always linear—it is a process that occurs over time.</p>
    <p class="teal-lead abs" style="left:20px;top:281px;width:205px">Your care will typically progress through the following stages:</p>
    <ul class="bullets abs" style="left:20px;top:317px;width:210px">
      <li><span class="stage-title">Relief Care</span><p class="stage-text">Focused on reducing discomfort and calming the body</p></li>
      <li style="margin-top:8px"><span class="stage-title">Corrective Care</span><p class="stage-text">Focused on addressing underlying issues and improving function (This phase may include prescribed exercises)</p></li>
      <li style="margin-top:8px"><span class="stage-title">Maintenance / Wellness Care</span><p class="stage-text">Focused on sustaining progress, preventing recurrence, and supporting long-term health</p></li>
    </ul>
  </div>
</section>

</body>
</html>
```